Copper Lantern

Need a business card for our restaurant. Restaurant and Bar in the mountains of North Idaho. Rustic looking card

rustic design, wood and metal looking, primarily neutral colors

• Name, address, phone number, website, email address

```html
<!DOCTYPE html>
<html lang="en">
<head>
<meta charset="utf-8">
<title>Copper Lantern – Business Card</title>
<link href="https://fonts.googleapis.com/css2?family=Lato:wght@400;700&display=swap" rel="stylesheet">
<style>
  :root {
    --backdrop: #666666;
    --card-dark: #121212;
    --card-dark-edge: #1e1e1e;
    --card-light: #ffffff;
    --ink: #1a1a1a;
    --ink-soft: #444444;
    --rule: #9a9a9a;
  }
  * { margin: 0; padding: 0; box-sizing: border-box; }
  html, body {
    width: 1200px; height: 900px; overflow: hidden;
    background: var(--backdrop);
    font-family: "Lato", sans-serif;
  }
  .stage { position: relative; width: 1200px; height: 900px; }

  .card-front {
    position: absolute; left: 110px; top: 100px;
    width: 400px; height: 700px;
    border-radius: 22px;
    background: linear-gradient(160deg, var(--card-dark-edge), var(--card-dark));
    box-shadow: 0 18px 40px rgba(0,0,0,.35);
    overflow: hidden;
  }
  .front-pattern {
    position: absolute; inset: 0;
    background: radial-gradient(circle at 60% 30%, #2a2a2a 0%, #141414 60%, #0d0d0d 100%);
  }
  .front-name {
    position: absolute; left: 0; right: 0; top: 200px;
    text-align: center; color: var(--card-light);
    font-weight: 700; font-size: 22px; letter-spacing: 1px;
  }

  .card-back {
    position: absolute; left: 560px; top: 290px;
    width: 560px; height: 320px;
    border-radius: 26px;
    background: var(--card-light);
    box-shadow: 0 18px 40px rgba(0,0,0,.35);
    display: flex; align-items: center;
  }
  .brand {
    width: 230px; display: flex; flex-direction: column;
    align-items: center; gap: 14px;
  }
  .brand-dot {
    width: 18px; height: 18px; border-radius: 50%; background: var(--ink);
  }
  .brand-name {
    font-weight: 700; font-size: 24px; color: var(--ink); text-align: center;
  }
  .divider {
    width: 1px; height: 220px; background: var(--rule);
  }
  .details { padding-left: 30px; padding-right: 20px; color: var(--ink-soft); }
  .person-name { font-weight: 700; font-size: 28px; color: var(--ink); }
  .person-role { font-size: 18px; margin-top: 4px; }
  .address { font-size: 18px; line-height: 1.3; margin-top: 18px; }
  .contact-list { list-style: none; margin-top: 16px; font-size: 18px; }
  .contact-list li { display: flex; align-items: center; gap: 12px; line-height: 1.5; white-space: nowrap; }
  .contact-list svg { width: 16px; height: 16px; fill: var(--ink); flex: none; }
</style>
</head>
<body>
<main class="stage">
  <section class="card-front">
    <div class="front-pattern" role="img" aria-label="Embossed repeating pattern of the restaurant's symbol on black"></div>
    <p class="front-name">Copper Lantern</p>
  </section>

  <section class="card-back">
    <div class="brand">
      <span class="brand-dot"></span>
      <span class="brand-name">Copper Lantern</span>
    </div>
    <span class="divider"></span>
    <div class="details">
      <h1 class="person-name">Marcus Hale</h1>
      <p class="person-role">Owner</p>
      <p class="address">218 Ridge Pine Road<br>Pinecrest, ID 83999</p>
      <ul class="contact-list">
        <li><svg viewBox="0 0 16 16"><path d="M3.5 1l2.5 3-1.5 1.8c.8 1.9 2.3 3.4 4.2 4.2L10.5 8.5l3 2.5-1.2 3C7 14 2 9 2 3.7z"/></svg>208.555.0147</li>
        <li><svg viewBox="0 0 16 16"><path d="M1 3h14v10H1zM2 4.2v.6l6 4 6-4v-.6z"/></svg>hello@copperlantern.com</li>
        <li><svg viewBox="0 0 16 16"><path d="M8 1a7 7 0 100 14A7 7 0 008 1zm0 1.5c.4 0 1.4 1.3 1.8 4H6.2C6.6 3.8 7.6 2.5 8 2.5zM5 8h6c0 2-.6 4.3-3 5.4C5.6 12.3 5 10 5 8z"/></svg>www.copperlantern.com</li>
      </ul>
    </div>
  </section>
</main>
</body>
</html>
```